Redesign (8 documents) attached with brand guidelines - very quick/easy job!

We have 8 flyers/documents that we need put into the style of our new brand (see attached). So this is a simple rebrand exercise - complete with our brand guidelines (see attached)

I would need the designer to sign an NDA prior to taking this piece of work as I will be sharing newly branded documents with you prior to market release.

If these are done well we would as the same designer to work on a z-card designed brochure/POS

Brief:

- These are documents that customers would need to complete in order to book a particular service
- If you use images (ideally from Pelvano, so we don’t have to pay for them!)
- Icon ideas enclosed
-All the content on the brochures is required: but if you think it would 'flow better' in a different order that is fine.

Target Market(s)

Customers interested in receiving a particular service

Industry/Entity Type

Work

Font styles to use
Other font styles liked:
• Brandon (see brand guide)

Requirements
Must have
• A4
Nice to have
• New logo ideas
Should not have
• Anything out of brand guidleines

```html
<!DOCTYPE html>
<html lang="en">
<head>
<meta charset="utf-8">
<title>Vitalane – Health Objectives</title>
<link href="https://fonts.googleapis.com/css2?family=Raleway:wght@400;600;700&display=swap" rel="stylesheet">
<style>
  :root {
    --brand-blue: #1b9cc0;
    --brand-lime: #b6cc2c;
    --ink: #3d3d3d;
    --ink-soft: #5a5a5a;
    --rule: #c9c9c9;
    --paper: #ffffff;
  }
  * { box-sizing: border-box; margin: 0; padding: 0; }
  html, body { width: 848px; height: 1200px; overflow: hidden; background: var(--paper); }
  body { font-family: "Raleway", Arial, sans-serif; color: var(--ink); }
  .sheet { position: relative; width: 848px; height: 1200px; overflow: hidden; background: var(--paper); }

  .header-band { position: absolute; left: 0; top: 0; width: 848px; height: 180px; display: block; }
  .footer-band { position: absolute; left: 0; bottom: 0; width: 848px; height: 44px; display: block; }

  .brand-name {
    position: absolute; left: 70px; top: 64px;
    font-size: 38px; font-weight: 600; letter-spacing: 0.5px;
    color: #ffffff;
  }

  .form-title {
    position: absolute; left: 73px; top: 226px;
    font-size: 26px; font-weight: 400; letter-spacing: 0.3px; color: var(--ink);
  }
  .meta-field {
    position: absolute; font-size: 13px; color: var(--ink-soft); white-space: nowrap;
  }

  .reason-bar {
    position: absolute; left: 73px; width: 706px; height: 30px;
    background: var(--brand-blue); border-radius: 15px;
    color: #fff; font-size: 14px; font-weight: 700;
  }
  .reason-bar span { position: absolute; top: 6px; }
  .reason-bar .reason-label { left: 17px; }
  .reason-bar .comments-label { left: 267px; }

  .row { position: absolute; left: 73px; width: 706px; display: flex; }
  .row .prompt, .row .answer {
    border: 1px solid var(--rule); border-radius: 12px; background: var(--paper);
  }
  .row .prompt {
    width: 251px; padding: 0 36px 0 17px; display: flex; align-items: center;
    font-size: 10.7px; line-height: 1.5; color: var(--ink-soft);
  }
  .row .answer { flex: 1; }
</style>
</head>
<body>
<main class="sheet">
  <svg class="header-band" viewBox="0 0 848 180" preserveAspectRatio="none" aria-hidden="true">
    <path d="M0 0 H848 V120 Q424 175 0 150 Z" fill="var(--brand-blue)"/>
    <path d="M0 162 Q424 190 848 132 V140 Q424 198 0 170 Z" fill="var(--brand-lime)"/>
  </svg>
  <div class="brand-name">Vitalane</div>

  <h1 class="form-title">HEALTH OBJECTIVES</h1>
  <p class="meta-field" style="left:73px;top:276px">Nutritionist’s name: ...................................................</p>
  <p class="meta-field" style="left:452px;top:276px">Client’s name: ...........................................................</p>
  <p class="meta-field" style="left:73px;top:318px">Store location: ............................................................</p>
  <p class="meta-field" style="left:452px;top:318px">Date of consultation:...............................................</p>

  <section class="reason">
    <div class="reason-bar" style="top:353px"><span class="reason-label">Reason 1</span><span class="comments-label">Your comments</span></div>
    <div class="row" style="top:388px;height:83px"><div class="prompt">Symptom, issue or condition you want to address.</div><div class="answer"></div></div>
    <div class="row" style="top:473px;height:83px"><div class="prompt">Duration - how long have you felt like this or experienced this symptom(s)?</div><div class="answer"></div></div>
    <div class="row" style="top:559px;height:83px"><div class="prompt">Have you seen a doctor about this for a diagnosis? Did you receive any medical treatment?</div><div class="answer"></div></div>
    <div class="row" style="top:645px;height:88px"><div class="prompt">Is there any background or extra health or lifestyle information that relates to this situation that you want your practitioner to know about? Please give details.</div><div class="answer"></div></div>
  </section>

  <section class="reason">
    <div class="reason-bar" style="top:745px"><span class="reason-label">Reason 2</span><span class="comments-label">Your comments</span></div>
    <div class="row" style="top:779px;height:84px"><div class="prompt">Symptom, issue or condition you want to address.</div><div class="answer"></div></div>
    <div class="row" style="top:865px;height:83px"><div class="prompt">Duration - how long have you felt like this or experienced this symptom(s)?</div><div class="answer"></div></div>
    <div class="row" style="top:951px;height:84px"><div class="prompt">Have you seen a doctor about this for a diagnosis? Did you receive any medical treatment?</div><div class="answer"></div></div>
    <div class="row" style="top:1037px;height:90px"><div class="prompt">Is there any background or extra health or lifestyle information that relates to this situation that you want your practitioner to know about? Please give details.</div><div class="answer"></div></div>
  </section>

  <svg class="footer-band" viewBox="0 0 848 44" preserveAspectRatio="none" aria-hidden="true">
    <rect x="0" y="0" width="848" height="4" fill="var(--brand-lime)"/>
    <rect x="0" y="12" width="848" height="32" fill="var(--brand-blue)"/>
  </svg>
</main>
</body>
</html>
```